*YO!!! Designers Needed!!* Front Page Cover Needed for a $$Billion Dollar$$ Company

We are a manufacturer of aluminum electrolytic capacitors. We are looking to create a front page cover that will be used on our annual report. We are a publicly listed company and work with many Meridex 400 companies, so your work will be viewed by the BIG GUNS and EXECUTIVES around the WORLD! If selected, you may be selected for additional work.

The front page cover should be unique. If elegance, modern, bling, and creativity somehow got together and had a child, that's what the cover page would look like!

Inspired Examples attached. Check them out!

www.brovanta.com

Font styles to use
Sans Serif

Requirements
Must have
• 1. Must include the attached logo. Logo size, color, and placement are at your discretion.

2. Should include the text, '2020 Annual Report'

3. The design should incorporate the use of foil and/or be embossed. The foil can be part of the design or can be the full page. See various examples attached for reference.

4. Shall be in A4 size and vertical orientation.
Nice to have
• Feel free to add any icons or stock photos (for example capacitors or circuit boards) if needed.

Be creative here and don't be afraid to be bold! The end product will be printed and budget is not a limiting factor, so feel free to make it extravagant if needed.

Our slogan is "Think Ahead". This slogan can or cannot be part of the theme.

```html
<!DOCTYPE html>
<html lang="en">
<head>
<meta charset="utf-8">
<title>Brovanta Annual Report 2020 Cover</title>
<link rel="stylesheet" href="https://fonts.googleapis.com/css2?family=Josefin+Sans:wght@300;400;600;700&display=swap">
<style>
  :root {
    --backdrop: #0b0b0b;
    --cover: #161616;
    --gold: #d8b66e;
    --gold-light: #f0d9a0;
    --gold-deep: #a9843f;
  }
  * { margin: 0; padding: 0; box-sizing: border-box; }
  html, body {
    width: 1124px;
    height: 1200px;
    overflow: hidden;
    background: var(--backdrop);
    font-family: "Josefin Sans", sans-serif;
  }
  .cover {
    position: absolute;
    left: 137px;
    top: 0;
    width: 849px;
    height: 1200px;
    background: var(--cover);
    overflow: hidden;
  }
  .gold-text {
    background: linear-gradient(100deg, var(--gold-deep), var(--gold-light) 45%, var(--gold) 70%, var(--gold-deep));
    -webkit-background-clip: text;
    background-clip: text;
    color: transparent;
  }
  .frame {
    position: absolute;
    left: 0;
    top: 0;
    width: 849px;
    height: 1200px;
  }
  .brand-name {
    position: absolute;
    left: 86px;
    top: 126px;
    font-weight: 600;
    font-size: 72px;
    line-height: 1;
    letter-spacing: 0.01em;
    color: var(--gold);
  }
  .title {
    position: absolute;
    left: 84px;
    top: 652px;
    font-weight: 300;
    font-size: 104px;
    line-height: 106px;
    letter-spacing: 0.06em;
  }
  .title-rule {
    position: absolute;
    left: 86px;
    top: 881px;
    width: 231px;
    height: 4px;
    background: linear-gradient(90deg, var(--gold-deep), var(--gold-light), var(--gold));
  }
  .year {
    position: absolute;
    left: 84px;
    top: 905px;
    font-weight: 700;
    font-size: 72px;
    line-height: 1;
  }
  .website {
    position: absolute;
    left: 86px;
    top: 1086px;
    font-weight: 300;
    font-size: 18px;
    letter-spacing: 0.32em;
    text-transform: uppercase;
  }
  .component-art {
    position: absolute;
    left: 673px;
    top: 656px;
    width: 176px;
    height: 544px;
    background: linear-gradient(180deg, rgba(216,182,110,0.18), rgba(216,182,110,0.06));
  }
</style>
</head>
<body>
  <main class="cover">
    <svg class="frame" viewBox="0 0 849 1200" aria-hidden="true">
      <defs>
        <linearGradient id="foil" x1="0" y1="0" x2="1" y2="1">
          <stop offset="0" stop-color="#a9843f"/>
          <stop offset="0.45" stop-color="#f0d9a0"/>
          <stop offset="1" stop-color="#c9a257"/>
        </linearGradient>
      </defs>
      <polyline points="819,631 819,48 34,48 34,1159 747,1159" fill="none" stroke="url(#foil)" stroke-width="4.5"/>
    </svg>

    <p class="brand-name">Brovanta</p>

    <h1 class="title gold-text">ANNUAL<br>REPORT</h1>
    <div class="title-rule"></div>
    <p class="year gold-text">2020</p>

    <p class="website gold-text">www.brovanta.com</p>

    <div class="component-art" role="img" aria-label="Gold foil line drawing of an electrolytic capacitor with its two leads running to the bottom edge"></div>
  </main>
</body>
</html>
```